Make it cool to work near where you are...

Calling all creatives - create the ultimate cool card for people who want to cut their commute.

Here at PineNook we've got what can best be described as an Flintpass card for desks - and we want to brighten up the wallets of our most loyal users.

So, pitch us your ideas and you might see your design on cards being flashed across the country - and we've thrown in a bit of cash too.

Do see our brief card guidelines - with a couple of past examples thrown in.

```html
<!DOCTYPE html>
<html lang="en">
<head>
<meta charset="utf-8">
<title>PineNook business card</title>
<link rel="stylesheet" href="https://fonts.googleapis.com/css2?family=Lato:wght@400;700;900&display=swap">
<style>
  :root {
    --backdrop: #d3dee5;
    --card: #fbfbfb;
    --pink: #e91e7a;
    --ink: #2f2f2f;
    --body: #333333;
  }
  * { margin: 0; padding: 0; box-sizing: border-box; }
  html, body { width: 1200px; height: 960px; overflow: hidden; }
  body {
    background: var(--backdrop);
    font-family: "Lato", sans-serif;
    color: var(--body);
    position: relative;
  }
  .card {
    position: absolute;
    left: 285px;
    width: 629px;
    height: 359px;
    border-radius: 22px;
    background: var(--card);
    overflow: hidden;
  }
  .card--front { top: 94px; }
  .card--back { top: 506px; }

  .wordmark {
    font-family: "Lato", sans-serif;
    font-weight: 900;
    color: var(--pink);
    letter-spacing: -0.02em;
    white-space: nowrap;
  }
  .card--front .wordmark {
    position: absolute;
    left: 0; right: 0;
    top: 128px;
    text-align: center;
    font-size: 92px;
    line-height: 1;
  }
  .front-url {
    position: absolute;
    left: 0; right: 0;
    top: 308px;
    text-align: center;
    font-size: 19px;
    font-weight: 700;
    color: var(--ink);
  }
  .card--back .wordmark {
    position: absolute;
    right: 44px;
    top: 36px;
    font-size: 40px;
    line-height: 1;
  }
  .contact {
    position: absolute;
    left: 63px;
    top: 142px;
    font-size: 15px;
    line-height: 18px;
  }
  .contact__name {
    color: var(--pink);
    font-weight: 700;
    font-size: 19px;
    line-height: 22px;
  }
  .contact__role { margin-bottom: 18px; }
  .contact__address { margin-bottom: 20px; }
  .contact__line {
    display: flex;
    align-items: center;
    gap: 8px;
    height: 20px;
  }
  .contact__icon { width: 17px; height: 17px; flex: none; }
</style>
</head>
<body>
  <section class="card card--front">
    <div class="wordmark">PineNook</div>
    <div class="front-url">www.PineNook.com</div>
  </section>

  <section class="card card--back">
    <div class="wordmark">PineNook</div>
    <div class="contact">
      <div class="contact__name">Alex Marlow</div>
      <div class="contact__role">Managing Director</div>
      <div class="contact__address">NookHouse, 48-52 Harrow Lane<br>E2 7QT London, United Kingdom</div>
      <div class="contact__line">
        <svg class="contact__icon" viewBox="0 0 16 16" aria-hidden="true">
          <path fill="#e91e7a" d="M2 5c0-2 2-3 6-3s6 1 6 3v1h-3V4.8C10 4.3 9 4 8 4s-2 .3-3 .8V6H2z"/>
          <path fill="#e91e7a" d="M4 7h8l2 7H2z"/>
          <circle cx="8" cy="10.5" r="1.6" fill="#fbfbfb"/>
        </svg>
        <span>+44 20 7946 0321</span>
      </div>
      <div class="contact__line">
        <svg class="contact__icon" viewBox="0 0 16 16" aria-hidden="true">
          <rect x="1" y="3" width="14" height="10" fill="#e91e7a"/>
          <path d="M1.5 3.5 8 9l6.5-5.5" fill="none" stroke="#fbfbfb" stroke-width="1.3"/>
        </svg>
        <span>team@pinenook.com</span>
      </div>
      <div class="contact__line">
        <svg class="contact__icon" viewBox="0 0 16 16" aria-hidden="true">
          <g fill="none" stroke="#e91e7a" stroke-width="1.4">
            <circle cx="8" cy="8" r="6.5"/>
            <ellipse cx="8" cy="8" rx="2.8" ry="6.5"/>
            <path d="M1.5 8h13M2.6 4.6h10.8M2.6 11.4h10.8"/>
          </g>
        </svg>
        <span>www.pinenook.com</span>
      </div>
    </div>
  </section>
</body>
</html>
```